Help our Sugar Loom find our winning design! We're looking for a business card....

We’re a Sugar Loom in NY specializing in custom-made cakes and unique desserts.
Our cakes combine flavor and art, each designed to match customer’s special event and theme.
We’d like a unique business card with a clean design that will combine French chic and artistic look & feel.
We’d like to differentiate ourselves from standard bakeries, please don’t offer cupcake images :-)
Our logo is peach-pink and brown and we’d love to use these colors ( . Another color that can be added is gold - or feel free to suggest!

Target Market(s)

Women, ages 25-55

Industry/Entity Type

Boutique

Contact Information for Business Card

Text on card:
Logo
Sugar Loom by Dana Welch

www.sugarloomsweets.com
hello@sugarloom.com
(516) 555-0147
F – sugarloomnyc
IG - sugarloom_ny

Font styles to use
Sans Serif
Script

Requirements
Must have
• Logo
• Clean look
• French chic and artistic look & feel.
Nice to have
• Damask pattern
Should not have
• Cupcake images

```html
<!DOCTYPE html>
<html lang="en">
<head>
<meta charset="utf-8">
<title>Sugar Loom – Business Card</title>
<link rel="stylesheet" href="https://fonts.googleapis.com/css2?family=Open+Sans:wght@400;600&family=Pinyon+Script&display=swap">
<style>
  :root {
    --backdrop: #e4e4e4;
    --card: #ffffff;
    --brown: #2f2624;
    --peach: #e3b3a6;
    --gold: #c9a040;
    --gold-light: #e8c976;
    --text: #3a3533;
  }
  * { box-sizing: border-box; margin: 0; padding: 0; }
  html, body { width: 1200px; height: 852px; overflow: hidden; }
  body {
    background: var(--backdrop);
    font-family: "Open Sans", Arial, sans-serif;
    color: var(--text);
    position: relative;
  }
  .card {
    position: absolute;
    top: 277px;
    width: 520px;
    height: 298px;
    background: var(--card);
    border-radius: 22px;
    box-shadow: 0 6px 18px rgba(0,0,0,0.12);
    border-bottom: 5px solid var(--gold);
    overflow: hidden;
  }
  .card--front { left: 60px; }
  .card--back { left: 620px; }

  .brand {
    position: absolute;
    display: flex;
    align-items: center;
    gap: 12px;
  }
  .brand__dot {
    width: 14px; height: 14px;
    border-radius: 50%;
    background: var(--peach);
  }
  .brand__name {
    font-family: "Pinyon Script", cursive;
    color: var(--brown);
    font-weight: 400;
    line-height: 1;
  }
  .card--front .brand { left: 0; right: 0; top: 112px; justify-content: center; }
  .card--front .brand__name { font-size: 64px; }
  .card--back .brand { left: 30px; width: 220px; top: 128px; justify-content: center; }
  .card--back .brand__name { font-size: 40px; }
  .card--back .brand__dot { width: 10px; height: 10px; }

  .divider {
    position: absolute;
    left: 268px; top: 40px;
    width: 1px; height: 220px;
    background: linear-gradient(to bottom, rgba(201,160,64,0), var(--gold) 30%, var(--gold) 70%, rgba(201,160,64,0));
  }
  .owner { position: absolute; left: 296px; top: 52px; }
  .owner__line { font-size: 15px; letter-spacing: 0.2px; }
  .owner__name {
    font-family: "Pinyon Script", cursive;
    font-size: 32px;
    color: var(--brown);
    line-height: 1.1;
  }
  .contacts {
    position: absolute;
    left: 296px; top: 150px;
    list-style: none;
  }
  .contacts li {
    display: flex;
    align-items: center;
    gap: 8px;
    font-size: 12px;
    line-height: 19px;
  }
  .contacts .icon {
    width: 12px; height: 12px;
    border-radius: 2px;
    background: linear-gradient(135deg, var(--gold-light), var(--gold));
    flex: none;
  }
</style>
</head>
<body>
  <section class="card card--front" aria-label="Card front">
    <div class="brand">
      <span class="brand__dot"></span>
      <span class="brand__name">Sugar Loom</span>
    </div>
  </section>

  <section class="card card--back" aria-label="Card back">
    <div class="brand">
      <span class="brand__dot"></span>
      <span class="brand__name">Sugar Loom</span>
    </div>
    <div class="divider"></div>
    <div class="owner">
      <p class="owner__line">Sugar Loom by</p>
      <p class="owner__name">Dana Welch</p>
    </div>
    <ul class="contacts">
      <li>
        <svg class="icon" viewBox="0 0 12 12" aria-hidden="true"><rect width="12" height="12" rx="2" fill="#c9a040"/><path d="M3 3.5c0 3 2.5 5.5 5.5 5.5l.8-1.3-1.6-.8-.7.7c-1-.4-1.8-1.2-2.2-2.2l.7-.7-.8-1.6z" fill="#fff"/></svg>
        (516) 555-0147
      </li>
      <li>
        <svg class="icon" viewBox="0 0 12 12" aria-hidden="true"><rect width="12" height="12" rx="2" fill="#c9a040"/><rect x="2.5" y="3.5" width="7" height="5" fill="none" stroke="#fff" stroke-width="0.9"/><path d="M2.5 3.5 6 6.3 9.5 3.5" fill="none" stroke="#fff" stroke-width="0.9"/></svg>
        hello@sugarloom.com
      </li>
      <li>
        <svg class="icon" viewBox="0 0 12 12" aria-hidden="true"><rect width="12" height="12" rx="2" fill="#c9a040"/><circle cx="6" cy="6" r="3.3" fill="none" stroke="#fff" stroke-width="0.9"/><path d="M2.7 6h6.6M6 2.7c-1.6 2-1.6 4.6 0 6.6M6 2.7c1.6 2 1.6 4.6 0 6.6" fill="none" stroke="#fff" stroke-width="0.7"/></svg>
        www.sugarloomsweets.com
      </li>
      <li><span class="icon"></span>sugarloomnyc</li>
      <li><span class="icon"></span>sugarloom_ny</li>
    </ul>
  </section>
</body>
</html>
```